Brochure "competition" request for funds for dry toilets PMR

We would like to participate in a contest to raise funds for our associations. These funds will be used to install dry toilets accessible to people in wheelchairs in order to make an activity center attractive to people with reduced mobility. If this contest leads to a positive response, we will be able to develop the activity of cross-country skiing, walks on landscaped paths, accessibility to a picnic spot, etc...

We are located in a mountain tourist region and the objective of our association is to make as many activities as possible possible for people with disabilities.

Target Market(s)

Our project will be presented to the bank carrying out the competition

Industry/Entity Type

Tourisme de personnes en situation de handicap

Colors
EB3D1F
EC4F4E
F09395
F8D3D4
FCEDEE

Requirements
Must have
• We have a website: www.velmoraccueil-asso.ch (still being finalized). We wish to have a bit of the same style of design as this one. Important: in the .docx file, the text is in French and it must remain so. The date of 3 days is imperative because we received the authorizations late and we have few days left to submit the project. The theme of the project is not "glamour" but necessary to allow these people to be able to practice activities. This is why it is important to obtain a presentation medium that inspires.
Nice to have
• If possible, it should be able to stay on a brochure with 4 A4 pages (= A3 horizontal double-sided)
Should not have
• It is not necessary to put too many images of illustration unrelated to the theme. We do not want medical style handicap photos, we are in tourism and we must favor the "outdoors - joie de vivre" style

```html
<!DOCTYPE html>
<html lang="fr">
<head>
<meta charset="utf-8">
<title>Velmor Accueil Association – Brochure toilette sèche PMR</title>
<link href="https://fonts.googleapis.com/css2?family=Exo+2:ital,wght@1,800;1,900&family=Arimo:wght@400;700&display=swap" rel="stylesheet">
<style>
:root{
  --red:#e63b21;
  --red-soft:#ec4f4e;
  --pink:#f09395;
  --pink-pale:#f8d3d4;
  --blush:#fcedee;
  --grey-band:#6d6d6d;
  --grey-page:#dcdcdc;
  --ink:#2b2b2b;
  --black:#141414;
  --bg:#e9e9e9;
  --white:#ffffff;
}
*{margin:0;padding:0;box-sizing:border-box}
html,body{width:1200px;height:3106px;overflow:hidden;background:var(--bg)}
body{font-family:"Arimo",Arial,sans-serif;color:var(--ink);position:relative}
.spread{position:absolute;left:40px;width:1120px;height:792px;display:flex;box-shadow:0 10px 30px rgba(0,0,0,.18)}
.spread--outer{top:731px}
.spread--inner{top:1583px}
.page{position:relative;width:560px;height:792px;overflow:hidden;background:var(--grey-page)}
.page + .page{border-left:1px solid rgba(0,0,0,.12)}
.abs{position:absolute}
.display{font-family:"Exo 2",Arial,sans-serif;font-style:italic;font-weight:900;text-transform:uppercase;letter-spacing:.5px}
.red-block{background:var(--red)}
.band{background:var(--grey-band);color:var(--white)}
.photo{position:absolute}
.brand{font-family:"Arimo",Arial,sans-serif;font-weight:700;color:var(--white);display:flex;align-items:center;gap:10px;text-transform:uppercase;line-height:1.05}
.brand-mark{width:16px;height:16px;background:var(--white);flex:none}

/* committee */
.committee-title{left:0;width:560px;top:30px;text-align:center;color:var(--white);font-size:33px}
.members{left:30px;top:100px;width:500px;display:flex;justify-content:space-between}
.member{width:100px;text-align:center;color:var(--white);font-size:9.5px;line-height:1.3}
.member b{display:block}
.avatar{width:60px;height:60px;border-radius:50%;margin:0 auto 8px;border:1.5px solid var(--white)}
.avatar--photo{background:radial-gradient(circle at 50% 40%,#c9a98f,#7b6a60)}
.budget-band{left:0;top:270px;width:560px;height:52px;font-size:20px;padding:13px 0 0 100px}
.budget{left:100px;top:340px;width:390px;font-size:10px;line-height:1.35;text-transform:uppercase;font-weight:700}
.budget .row{display:flex;justify-content:space-between}
.budget .amount{color:var(--red);font-weight:400;width:80px}
.budget .sub{font-weight:400;text-transform:none;padding-left:28px}
.budget .gap{height:12px}

/* cover */
.cover-title{left:25px;top:150px;color:var(--white);font-size:14px;line-height:1.35}
.cover-sub{left:25px;top:235px;color:var(--white);font-size:13px}
.intro-band{left:0;top:270px;width:560px;height:52px;font-size:9.5px;font-weight:700;line-height:1.4;padding:11px 25px}
.specs{left:22px;top:340px;width:170px}
.specs h3{color:var(--red);font-size:17px}
.specs .dim{font-size:10px;margin-bottom:14px}
.spec{display:flex;gap:8px;font-size:10px;margin-bottom:22px}
.spec i{width:12px;height:12px;border:1.2px solid var(--ink);flex:none;margin-top:2px}
.spec b{display:block;color:var(--red)}
.note{color:var(--red);font-size:8.5px;line-height:1.3}

/* objectives */
.obj-title{left:0;width:560px;top:28px;text-align:center;color:var(--white);font-size:25px;line-height:1.3}
.goal{color:var(--white);font-size:9px;line-height:1.35;position:absolute}
.goal svg{display:block;margin-bottom:6px}
.status-band{left:0;top:375px;width:560px;height:42px;background:var(--black);color:var(--red);font-size:23px;text-align:center;padding-top:7px}
.mountain{left:0;top:417px;width:560px;height:375px;background:linear-gradient(180deg,#b9c7d6 0%,#dbe3ec 55%,#f3f5f8 75%,#8f96a0 100%)}
.statut-text{left:30px;top:440px;width:500px;font-size:9px;line-height:1.4}
.statut-text h4{color:var(--red);font-size:12px;margin-bottom:6px}
.statut-text .ref{font-size:8.5px}

/* strengths */
.str-title{left:20px;top:20px;color:var(--red);font-size:24px}
.strengths{left:20px;top:62px;width:520px;font-size:9px;line-height:1.4}
.strengths li{list-style:none;margin-bottom:10px}
.strengths li::before{content:"•";margin-right:20px}
.link{color:var(--red);display:block}
.region{left:20px;top:245px;width:250px;font-size:8.5px;line-height:1.4}
.infra{left:0;top:375px;width:560px;height:417px;background:linear-gradient(180deg,#a9b9cb 0%,#cfd9e5 50%,#eef1f5 75%,#838b96 100%)}
.infra-title{left:0;width:560px;top:400px;text-align:center;color:var(--red);font-size:24px}
.infra-text{left:70px;top:455px;font-size:9px;line-height:1.4}
</style>
</head>
<body>

<section class="spread spread--outer">
  <article class="page page--committee">
    <div class="abs red-block" style="left:0;top:0;width:560px;height:270px"></div>
    <h2 class="abs display committee-title">Membres du comite</h2>
    <div class="abs members">
      <div class="member"><div class="avatar avatar--photo" role="img" aria-label="Portrait de la présidente"></div><b>Morand Élise</b>Présidente</div>
      <div class="member"><div class="avatar avatar--photo" role="img" aria-label="Portrait du caissier"></div><b>Rey-Mottet Julien</b>Caissier</div>
      <div class="member"><div class="avatar avatar--photo" role="img" aria-label="Portrait de la secrétaire"></div><b>Rey-Mottet Sandrine</b>Secrétaire</div>
      <div class="member"><div class="avatar"></div><b>Clavel Loïc</b>Membres</div>
      <div class="member"><div class="avatar"></div><b>Fardel Mathieu</b>Membres</div>
    </div>
    <h3 class="abs band display budget-band">Budget d'avant projet (+/-20%)</h3>
    <div class="photo" role="img" aria-label="Forêt de sapins et prairie de montagne" style="left:0;top:640px;width:560px;height:152px;background:linear-gradient(180deg,rgba(220,220,220,0) 0%,#8a9c8a 30%,#4d6b4a 70%,#3d6a37 100%)"></div>
    <svg class="abs" style="left:0;top:605px" width="560" height="70" viewBox="0 0 560 70" aria-hidden="true"><polygon points="0,70 0,55 190,8 230,30 330,4 560,62 560,70" fill="#e63b21" opacity=".55"/></svg>
    <div class="abs budget">
      <div class="row"><span>1. Autorisations communales <span style="font-weight:400;text-transform:none">(si nécessaire)</span></span><span class="amount">CHF &nbsp;&nbsp;&nbsp;500.-</span></div>
      <div class="row"><span>2. Installation de chantier</span><span class="amount">CHF &nbsp;&nbsp;&nbsp;500.-</span></div>
      <div class="row"><span>3. Surface à goudronner (+/-10m2)</span><span class="amount">CHF &nbsp;1'500.-</span></div>
      <div class="row"><span>4. Terrassement et amenagement</span><span class="amount">CHF &nbsp;1'910.-</span></div>
      <div class="sub">•&nbsp;&nbsp;Drain inclus</div>
      <div class="gap"></div>
      <div class="row"><span>5. Installation, équipements</span><span></span></div>
      <div class="row sub"><span>•&nbsp;&nbsp;Toilette sèche PMR + urinoir extérieur</span><span class="amount">CHF 10'000.-</span></div>
      <div class="row sub"><span>•&nbsp;&nbsp;Luminaire LED sur panneau solaire</span><span class="amount">CHF &nbsp;&nbsp;&nbsp;300.-</span></div>
      <div class="row sub"><span>•&nbsp;&nbsp;Système d'accès ClefAccès</span><span class="amount">CHF &nbsp;&nbsp;&nbsp;300.-</span></div>
      <div class="gap"></div>
      <div class="row"><span>6. Transport, modalites douanieres</span><span class="amount">CHF &nbsp;1'000.-</span></div>
      <div class="row"><span style="font-weight:400">Buget prévisionnel du WC PMR</span><span class="amount">CHF 16'010.-</span></div>
      <div class="row"><span style="font-weight:400">Option supplementaire:</span></div>
      <div class="gap"></div>
      <div class="row"><span>7. Amenagement d'une table accessible<br>en fauteuil sous le couvert</span><span class="amount">CHF &nbsp;1800.-</span></div>
      <div class="gap"></div>
      <div class="row"><span>Total projet</span><span class="amount" style="font-weight:700">CHF 17'810.-</span></div>
    </div>
    <div class="abs brand" style="left:135px;top:715px;font-size:24px"><span class="brand-mark"></span><span>Velmor Accueil<br>Association</span></div>
  </article>

  <article class="page page--cover">
    <div class="abs red-block" style="left:0;top:0;width:560px;height:270px"></div>
    <svg class="abs" style="left:380px;top:0" width="180" height="270" viewBox="0 0 180 270" aria-hidden="true"><polygon points="0,0 180,0 180,150" fill="#c7c7c7"/><polygon points="180,150 180,270 90,270" fill="#bdbdbd"/></svg>
    <div class="abs brand" style="left:25px;top:40px;font-size:20px"><span class="brand-mark"></span><span>Velmor Accueil<br>Association</span></div>
    <h1 class="abs display cover-title">Installation d'une toilette<br>sèche accessible PMR au<br>couvert du Grand Clos</h1>
    <p class="abs display cover-sub">Toilette sèche Alpa 2 PMR</p>
    <div class="photo" role="img" aria-label="Cabine de toilette sèche en bois au toit bleu" style="left:320px;top:28px;width:200px;height:225px;background:linear-gradient(160deg,#6d76b8 0%,#6d76b8 30%,#c58e64 32%,#a26d46 100%)"></div>
    <p class="abs band intro-band">Velmor Accueil Association est une association à but non lucratif crée en mai 2021. Son siège se situe à 1879 Velmor - Valais - Suisse, dans la Région Monts de Velmor (domaine des Balcons du Soleil).</p>
    <div class="abs specs">
      <h3 class="display">Toilette sèche</h3>
      <p class="dim">Dimensions HT :</p>
      <div class="spec"><i></i><span><b>Largeur</b>2.270 m</span></div>
      <div class="spec"><i></i><span><b>Profondeur</b>1,960 m</span></div>
      <div class="spec"><i></i><span><b>Hauteur</b>2,10 m</span></div>
      <p class="note">(mesures approximatives qui peuvent varier selon le choix final du fournisseur)</p>
    </div>
    <div class="photo" role="img" aria-label="Intérieur de la cabine en bois avec lucarne" style="left:190px;top:330px;width:105px;height:85px;background:linear-gradient(135deg,#c99a6c,#6b4b33)"></div>
    <div class="photo" role="img" aria-label="Distributeur et luminaire dans la cabine" style="left:305px;top:330px;width:120px;height:85px;background:linear-gradient(135deg,#d6b48d,#7a5a3d)"></div>
    <div class="photo" role="img" aria-label="Pique-nique en famille sur une table en bois dans la prairie" style="left:250px;top:420px;width:120px;height:90px;background:linear-gradient(180deg,#9bb27a,#5f7d45)"></div>
    <div class="photo" role="img" aria-label="Intérieur de toilette accessible" style="left:380px;top:460px;width:100px;height:145px;background:linear-gradient(180deg,#d2ab80,#806046)"></div>
    <div class="abs" style="left:430px;top:420px;width:50px;height:40px;border:1px solid var(--red);border-right:none;border-bottom:none"></div>
    <svg class="abs" style="left:0;top:580px" width="560" height="60" viewBox="0 0 560 60" aria-hidden="true"><polygon points="0,60 0,50 40,60 130,10 240,55 560,40 560,60" fill="#e63b21"/></svg>
    <div class="photo" role="img" aria-label="Deux cabines de toilettes sèches en bois sur l'herbe" style="left:0;top:620px;width:560px;height:172px;background:linear-gradient(180deg,#b58557 0%,#9a6c43 45%,#7b9b5e 75%,#5c8a44 100%)"></div>
  </article>
</section>

<section class="spread spread--inner">
  <article class="page page--objectives">
    <div class="abs" style="left:0;top:0;width:560px;height:375px;background:linear-gradient(90deg,var(--red),var(--red-soft))"></div>
    <h2 class="abs display obj-title">Les objectifs de<br>l'association sont :</h2>
    <div class="goal" style="left:30px;top:110px;width:120px">
      <svg width="28" height="22" viewBox="0 0 28 22" fill="none" stroke="#fff" stroke-width="1.8"><path d="M3 8h5l10-6v18l-10-6H3z"/><path d="M22 7c2 2 2 6 0 8"/></svg>
      Favoriser l'accueil et les loisirs des personnes en situation de handicap</div>
    <div class="goal" style="left:185px;top:110px;width:130px">
      <svg width="28" height="22" viewBox="0 0 28 22" fill="none" stroke="#fff" stroke-width="1.8"><path d="M4 14h8l6-5 4 3-8 7H4z"/><circle cx="18" cy="5" r="3"/></svg>
      Servir l'intérêt général des personnes en situation de handicap ainsi que soulager les proches aidants et accompagnants</div>
    <div class="goal" style="left:355px;top:110px;width:130px">
      <svg width="28" height="22" viewBox="0 0 28 22" fill="none" stroke="#fff" stroke-width="1.8"><rect x="13" y="2" width="11" height="18"/><path d="M3 11h10M9 7l4 4-4 4"/></svg>
      Permettre l'accès à des loisirs et l'accès à des lieux comme tout un chacun</div>
    <div class="goal" style="left:30px;top:230px;width:230px">
      <svg width="24" height="24" viewBox="0 0 24 24" fill="none" stroke="#fff" stroke-width="1.8"><circle cx="12" cy="12" r="10"/><circle cx="12" cy="10" r="3"/><path d="M6 19c2-4 10-4 12 0"/></svg>
      Sensibiliser et faire évoluer les représentations sociales, par des actions, communications, projets et évènements touchant et impliquant des partenaires associatifs, économiques, politiques, les médias et le public en général</div>
    <div class="goal" style="left:290px;top:230px;width:230px">
      <svg width="24" height="24" viewBox="0 0 24 24" fill="none" stroke="#fff" stroke-width="1.8"><path d="M12 22s-7-7-7-12a7 7 0 0114 0c0 5-7 12-7 12z"/><circle cx="12" cy="10" r="2.5"/></svg>
      Favoriser la collaboration auprès des acteurs locaux. Les ressources de l'association proviennent des cotisations, dons et manifestations organisées tout au long de l'année.</div>
    <h3 class="abs display status-band">Statuts de l'association</h3>
    <div class="photo mountain" role="img" aria-label="Sommets enneigés sous un ciel d'hiver"></div>
    <div class="abs statut-text">
      <p class="ref">C.f. annexe 1</p>
      <h4 class="display">Rapport de gestion</h4>
      <p class="ref">C.f. annexe 2</p>
      <h4 class="display">Présentation du projet</h4>
      <p>Nous posons notre candidature au prix humanitaire et social de la fondation du 100ème de la Banque Cantonale Alpine pour réunir les fonds nécessaires à l'achat, l'aménagement et l'équipement spécifique d'une toilette et d'une table adaptées au couvert du Grand Clos à Velmor-Village afin de rendre cet espace accessibles et attractif aux personnes en situation de handicap.<br>L'un des buts de Velmor Accueil Association est de permettre l'accès à des loisirs et l'accès à des lieux comme tout un chacun dans la Région Monts de Velmor.<br>Pour y parvenir et pouvoir proposer des activités, nous nous sommes donné la mission d'équiper ce lieu ciblé qui est le point de départ de multiples activités été comme hiver.</p>
    </div>
  </article>

  <article class="page page--strengths">
    <div class="abs" style="left:0;top:0;width:560px;height:375px;background:linear-gradient(180deg,#d0d0d0,#e4e4e4)"></div>
    <h2 class="abs display str-title">Forces et atouts du projet</h2>
    <div class="abs strengths">
      <p style="margin-bottom:2px">Lorsque ce lieu sera équipé, les personnes à mobilités réduites pourront :</p>
      <ul>
        <li>Partir l'assaut de la piste de ski de fond en luge nordique<span class="link">www.montsdevelmor.ch/fr/ski-de-fond-grand-clos-boucle-eclairee</span></li>
        <li>Prendre part à une agréable balade au « Chemin des poussettes » qui relie le village de Velmor-Village au Couvert<span class="link">www.montsdevelmor.ch/fr/chemin-des-poussettes</span></li>
        <li>Passer une agréable journée entre amis ou en famille au couvert<span class="link">www.montsdevelmor.ch/fr/couvert-du-grand-clos</span></li>
        <li>Participer à des évènements annuels divers tels que le Vélo et Musique, etc<span class="link">www.montsdevelmor.ch/fr/velo-et-musique-festival</span></li>
      </ul>
    </div>
    <p class="abs region">Les possibilités touristiques de la région étant multiples tout au long de l'année, nous pourrons dès réalisation de ce projet, collaborer avec Région Monts de Velmor pour augmenter l'offre réservée aux personnes à mobilité réduite.<br>La proximité avec la plaine et le lac Léman permet également d'étoffer l'offre touristique valaisanne</p>
    <svg class="abs" style="left:290px;top:220px" width="150" height="140" viewBox="0 0 150 140" aria-hidden="true"><polygon points="75,5 145,70 125,70 125,135 25,135 25,70 5,70" fill="#e63b21"/><rect x="40" y="72" width="70" height="55" fill="#ffffff"/></svg>
    <div class="photo" role="img" aria-label="Personne en luge nordique sur la neige" style="left:330px;top:292px;width:70px;height:55px;background:linear-gradient(180deg,#cfd8e2,#f2f4f7)"></div>
    <div class="photo infra" role="img" aria-label="Paysage de montagne enneigé"></div>
    <h2 class="abs display infra-title">Infrastructures</h2>
    <div class="abs infra-text">Le projet se base sur<br>•&nbsp; L'achat, l'aménagement et l'équipement d'une toilette adaptée<br>•&nbsp; L'achat d'une table en bois accessible aux personnes à mobilité réduite</div>
  </article>
</section>

</body>
</html>
```